Velmora Gems - High end custom Jewelry website

I need a web design for an online custom jewelry company called Velmora Gems. (www.velmoragems-demo.com) this company specializes in high-end custom made engagement rings, wedding bands and jewelry of all kinds (necklaces, earrings, bracelets etc)All our jewelry uses diamonds so there must be a focus on diamonds on every type of jewelry we will be designing off the website.

We are a company located in New York City but our website will
aim to cater to international, national clients and as well as New York city residents.The company low overhead provides diamonds and precious metal at a discounted costs compared to its competitors. Velmora Gems makes unique custom diamond jewelry of a higher quality and at a lower price than carriage trade retail jewellers. (meaning that our company allows our customers to save money on diamond jewelry then they would if they bought from any known store or company)

The website will act as a tool for our customers to create their own jewelry. The way they will do this is by uploading pictures of what they like, they can post any pictures they want (from drawings, to actual copy and pasted pictures from other websites of designs) From these designs we will create a 3D digital image of the jewelry they like and customize it - however they want (colours, size etc) and then give them a quote in price. From the quote they will either approve it and we can have it made for them in 1 weeks time. If they decline it we will try to do whatever it is they want for the design to suit their needs.

We want the website to be simple and user friendly since people will be working on it to create their own individual jewelry pieces. Therefore some useful headings should include:

"Custom Jewellery" or something like "your design" "Custom Design"

a drop heading here should show the following steps into creating the jewelry.

step 1:
upload pictures of the designs you like
step 2:
What is your ring size?
Step 3:
What setting would you like your ring in? platinum, 14k etc..
Step 4:
What is your budget?
Step 5 :
Once you’ve uploaded pictures and give an explanation of what you want then we will contact you by phone or email and proceed to design your ring. Give us your contact info in this step.

Other then that other headings id like to see on the site are:

"Home"
main page with appealing picture which I can later add text to it explaining our company

"About us"
will include a brief section of who we are

"Wedding/engagment"

We are based in New York City and our company offers a one-to-one personal service to our clients ensuring their expectations are well met and, if we can help it, surpassed. We are a personal shopping and diamond supplier to individuals. Custom design is our speciality weather it be wedding ring, engagement ring or anniversary ring we aim to create distinctive designs that both reflect your personality as well as the beauty of the gemstones used in your piece. We use platinum, 14l-18k gold and diamonds to whatever it is that you may desire.
We in our company believe that we are privileged to be a part of one of the biggest events in our customer’s lives, and we pride ourselves on making sure that our customers have the best experience possible. As the diamond is the center piece of every engagement ring, we at VG make sure that our clients find the best diamond possible that is within their budget. Similarly, we work with established jewellery artisans from Belgium to provide the highest possible craftsmanship to a ring design of your choice. We make sure that our rings are made by the true and tried traditional methods focused on quality rather than quantity and of course our diamonds are QRB certified.

Diamonds

A section that explains where our diamonds come from. A heading will drop down here that is a diamond guide, as shown below.
Diamond Guide

An overview of the 4 C’s and different settings, a section for a brief education on diamonds.
Client Experiences

A section where clients share their experiences with Velmora Gems and can post pictures and share stories about their engagement etc.

The colour i would like to see are white and black, white and dark blue or royal blue. I don't think pastel colours will look good with this, maybe accents of purple or something pastel but for the main colours I want to keep it classic and sophisticated since it is a diamond company.

"Sign in | Check out"
where users are able to create a profile and upload their pictures and create their designs..

and a "search section"

or something along these lines or if you can incorporate both:

Exquisite craftsmanship Finest quality diamonds
Will beat any competitors price by twenty to seventy percent guaranteed
Price quotes whitin24 hours

Upload design picture or sketch
Receive price quote within 24hours
Receive and approve free customized design
Receive you jewelry in 1 week or less

Engagment Ring or necklace, earring, etc
Name
EMail
phone
Competitior Link
Budget

The final design should communicate that Velmora Gems is a custom jewelry site that allows individuals to personalize any type of jewellery they want with diamonds - at a fraction of the cost in comparison to any other out there. Our team works very hard to ensure that you will be so involved in the custom order process that there is no chance of something not being made to your requests. Jewelry is made to the highest standard or it does not ship in the first place. In the event a custom order does not suit a customer, we will take returns within 14 days of delivery less a 25% restocking fee.

Target Market(s)

middle class and upper class people ages 25-45

Industry/Entity Type

Digital

Requirements
Must have
• We have the logo now that I will attach BUT if you want to design something else please feel free ! I am open to all designs and ideas.
My logo now is simply a sketch so even if we make it look a bit more professional and classy I would like that, I think I want to keep it simple just black and white and maybe make the diamond shiny if possible. other then black in white I liked the gold and black combination too.. but as I said open to any other creative ideas!

can take pictures of jewelry off this website:
http://www.plinthwaredesigns.example/library/rings.html
Nice to have
• We already have a logo but we would like to see a banner or something that indicated saving money on diamond jewelry without it looking tacky or too cheap..

Also would like to see artistic pictures if you can of jewelry alongside very simple designs of jewelry that the masses like, (anything trendy or appealing to the eye)

cursive or elegant writing could be nice, flash could also be incorporated in the main page..

Should not have
• Nothing to old fashioned, when I mean elegant maybe just the the name of the company in cursive writing (Velmora Gems) but the actual headings and font on the website to be in a widely used font on jewelry websites. Please no hot pink colours or anything neon..
no times new roman font..

```html
<!DOCTYPE html>
<html lang="en">
<head>
<meta charset="utf-8">
<title>Velmora Gems — Custom Diamond Jewellery</title>
<link href="https://fonts.googleapis.com/css2?family=Source+Sans+3:ital,wght@0,400;0,500;0,600;1,400&display=swap" rel="stylesheet">
<style>
:root{
  --ink:#111;
  --navy:#0b1f78;
  --royal:#0c10e6;
  --deep:#0a1560;
  --grey:#555;
  --line:#e2e2e2;
  --footer:#4a4a4a;
  --panel:#333;
}
*{margin:0;padding:0;box-sizing:border-box}
html,body{width:791px;height:1200px;overflow:hidden;background:#fff}
body{position:relative;font-family:"Source Sans 3",Arial,sans-serif;font-weight:400;color:var(--ink)}
.abs{position:absolute}
.topbar{left:0;top:0;width:791px;height:28px;background:#050505;color:#fff;font-size:9px;font-weight:500;letter-spacing:.2px}
.topbar .links{left:74px;top:8px;white-space:nowrap}
.topbar .links span{margin:0 8px;font-weight:400}
.topbar .cart{left:658px;top:8px;font-size:9.5px;display:flex;align-items:center;gap:5px}
.brand{left:58px;top:62px;display:flex;align-items:center;gap:8px}
.brand .mark{width:14px;height:14px;border-radius:50%;background:var(--ink)}
.brand .name{font-size:19px;font-weight:500;color:var(--ink)}
.search{left:584px;top:51px;width:149px;height:23px;border:1px solid #bbb;border-radius:3px;font-size:8.5px;font-style:italic;color:#999;padding:5px 4px}
.search svg{position:absolute;right:7px;top:6px}
.nav{top:97px;font-size:11px;font-weight:500;white-space:nowrap}
.hero{left:57px;top:126px;width:676px;height:262px;background:
  radial-gradient(ellipse 28% 45% at 22% 42%,rgba(210,212,222,.55),transparent 70%),
  radial-gradient(ellipse 28% 45% at 42% 42%,rgba(210,212,222,.55),transparent 70%),
  radial-gradient(ellipse 28% 45% at 60% 42%,rgba(210,212,222,.55),transparent 70%),
  radial-gradient(ellipse 28% 45% at 78% 42%,rgba(210,212,222,.55),transparent 70%),
  linear-gradient(180deg,#050507 0%,#111118 55%,#3b3a52 75%,#1a1a26 100%)}
.dots{left:689px;top:374px;display:flex;gap:2px}
.dots i{width:8px;height:8px;border:1px solid #ddd;border-radius:50%;background:#777}
.dots i:first-child{background:#ddd}
.welcome{left:0;top:408px;width:791px;text-align:center}
.welcome h1{font-size:16.5px;font-weight:500;color:var(--navy)}
.welcome p{width:622px;margin:9px auto 0;font-size:10.4px;line-height:18.5px;color:var(--grey)}
.btn{background:linear-gradient(#3a3a3a,#060606);color:#fff;border-radius:3px;text-align:center}
.readmore{left:365px;top:484px;width:81px;height:24px;font-size:10px;line-height:24px;box-shadow:0 1px 2px #888}
.divider{left:57px;top:522px;width:690px;height:6px;background:radial-gradient(ellipse at 50% 0,#e4e4e4,transparent 70%)}
.card{top:539px;width:215px;height:119px;border:1px solid var(--line)}
.card .photo{left:14px;top:18px;width:72px;height:85px}
.card h3{left:104px;top:17px;width:110px;font-size:10.4px;font-weight:400;line-height:16.5px;color:var(--navy)}
.card .price{left:107px;top:56px;font-size:10px;color:#222}
.card .more{left:110px;top:84px;width:72px;height:20px;font-size:8.5px;line-height:20px}
.sec-title{font-size:16px;font-weight:500;color:var(--navy)}
.post{left:57px;width:440px;height:110px}
.post .thumb{left:0;top:0;width:105px;height:98px;border:1px solid #ddd;padding:3px}
.post .thumb div{width:100%;height:100%}
.post h4{left:118px;top:0;font-size:11.5px;font-weight:500;color:var(--navy);white-space:nowrap}
.post p{left:118px;top:17px;width:316px;font-size:8.8px;line-height:14.2px;color:#333}
.post .date{left:116px;top:94px;font-size:7.5px;font-style:italic;color:#555}
.form{left:521px;top:711px;width:223px;height:226px;background:var(--royal)}
.form h5{left:13px;top:14px;font-size:11.5px;font-weight:500;color:#fff}
.form .field{left:14px;width:194px;height:24px;background:#fff;border-radius:2px;font-size:8.5px;color:#888;padding:6px 8px}
.form .submit{left:140px;top:195px;width:68px;height:22px;background:var(--deep);color:#fff;font-size:11.5px;font-weight:500;text-align:center;line-height:22px}
.custom{left:521px;top:957px;width:223px;height:81px;background:var(--panel);border-radius:2px;color:#fff}
.custom .icon{left:14px;top:8px;width:36px;height:36px;border-radius:50%;background:radial-gradient(circle,#f4f4f4,#9a9a9a)}
.custom h6{left:67px;top:7px;font-size:15px;font-weight:400}
.custom .sub{left:69px;top:30px;font-size:8.5px;font-weight:500}
.custom p{left:12px;top:48px;width:205px;font-size:7.2px;line-height:13.5px;color:#ddd}
.footer{left:0;top:1072px;width:791px;height:128px;background:var(--footer);color:#fff}
.fcol h6{font-size:11.5px;font-weight:400;margin-bottom:13px}
.fcol li{list-style:none;font-size:8.8px;font-weight:400;line-height:19px;display:flex;align-items:center;gap:6px}
.fcol li::before{content:"";width:4px;height:4px;border-radius:50%;background:#bbb;margin-left:-12px;margin-right:4px}
.promise li{font-size:9.6px;line-height:20px}
.copy{left:390px;top:99px;font-size:9px;color:#eee}
.social{top:98px;width:19px;height:19px;border-radius:50%;background:#5c5c5c}
</style>
</head>
<body>

<header>
  <div class="abs topbar">
    <div class="abs links">MY ACCOUNT<span>|</span>SIGN IN<span>|</span>CHECK OUT<span>|</span>CONTACT US</div>
    <div class="abs cart">
      <svg width="13" height="11" viewBox="0 0 13 11"><path d="M0 1h2.5l1.6 6h6.4L12 3H3.3" fill="none" stroke="#fff" stroke-width="1"/><circle cx="5" cy="9.5" r="1" fill="#fff"/><circle cx="9.5" cy="9.5" r="1" fill="#fff"/></svg>
      Cart (0) items
    </div>
  </div>

  <div class="abs brand"><span class="mark"></span><span class="name">Velmora Gems</span></div>

  <div class="abs search">Search..
    <svg width="9" height="9" viewBox="0 0 9 9"><circle cx="3.6" cy="3.6" r="2.8" fill="none" stroke="#888" stroke-width="1.2"/><path d="M5.7 5.7L8.5 8.5" stroke="#888" stroke-width="1.3"/></svg>
  </div>

  <nav>
    <span class="abs nav" style="left:363px">HOME</span>
    <span class="abs nav" style="left:418px">ABOUT US</span>
    <span class="abs nav" style="left:491px">PRODUCTS</span>
    <span class="abs nav" style="left:568px">SERVICES</span>
    <span class="abs nav" style="left:637px">BLOG</span>
    <span class="abs nav" style="left:688px">CONTACT</span>
  </nav>
</header>

<section class="abs hero" role="img" aria-label="Photograph: four diamond solitaire rings in white gold standing in a row, reflected on a dark glossy surface"></section>
<div class="abs dots"><i></i><i></i><i></i><i></i></div>

<section class="abs welcome">
  <h1>Welcome to our Website</h1>
  <p>Claritas est etiam processus dynamicus, qui sequitur mutationem consuetudium lectorum. Mirum est notare quam littera gothica, quai minunc putamus parum claram, anteposuerit litterarum in the formas humanitatis per seacula quarta decima et quinta decima.</p>
</section>
<div class="abs btn readmore">READ MORE</div>
<div class="abs divider"></div>

<section>
  <article class="abs card" style="left:57px">
    <div class="abs photo" role="img" aria-label="Photograph: silver crescent moon pendant with a small star on a fine chain" style="background:radial-gradient(ellipse at 50% 65%,#c4c4ca,#eeeeef 55%,#fff)"></div>
    <h3 class="abs">Lunessa Brilliant Halo Pavé Setting</h3>
    <div class="abs price">Price : $146.00 (-3%)</div>
    <div class="abs btn more">MORE DETAILS</div>
  </article>
  <article class="abs card" style="left:287px">
    <div class="abs photo" role="img" aria-label="Photograph: pair of leaf shaped earrings set with blue sapphires and diamonds" style="background:radial-gradient(ellipse 30% 45% at 30% 50%,#2b2f6a,#c9cad4 80%,#fff),radial-gradient(ellipse 30% 45% at 72% 50%,#d6d6dc,#fff 80%)"></div>
    <h3 class="abs">Lunessa Brilliant Halo Pavé Setting</h3>
    <div class="abs price">Price : $146.00 (-3%)</div>
    <div class="abs btn more">MORE DETAILS</div>
  </article>
  <article class="abs card" style="left:519px">
    <div class="abs photo" role="img" aria-label="Photograph: multi strand silver bead bracelet" style="background:radial-gradient(ellipse at 50% 50%,#fff 25%,#a9a9b0 45%,#e4e4e7 60%,#fff 75%)"></div>
    <h3 class="abs">Lunessa Brilliant Halo Pavé Setting</h3>
    <div class="abs price">Price : $146.00 (-3%)</div>
    <div class="abs btn more">MORE DETAILS</div>
  </article>
</section>

<section>
  <h2 class="abs sec-title" style="left:57px;top:681px">Recent Blog</h2>

  <article class="abs post" style="top:707px">
    <div class="abs thumb"><div role="img" aria-label="Photograph: loose round diamonds scattered on a dark surface" style="background:radial-gradient(circle at 60% 40%,#d8d8d8,#555 55%,#111)"></div></div>
    <h4 class="abs">Suspendisse eu erat quam. Vivamus porttitor eros quis.</h4>
    <p class="abs">Suspendisse eu erat quam. Vivamus porttitor eros quis nisi lacinia sed intierdum uam a orci quis nisi sagittis sagittis. Etiam adipiscing, justo quis feugiat.Suspend amus porttitor eros quis nisi lacinia sed interdum lorem vulputate. Etiam adipisc ing, justo quis feugiat.Suspendamus porttitor eros quis nisi lacinia sed interdum lorem vulputate.</p>
    <div class="abs date">Posted on 02 June, 2013</div>
  </article>

  <article class="abs post" style="top:825px">
    <div class="abs thumb"><div role="img" aria-label="Photograph: emerald cut amethyst ring with side diamonds on black" style="background:radial-gradient(circle at 50% 50%,#9a6fc4,#3d2557 50%,#050505)"></div></div>
    <h4 class="abs">Suspendisse eu erat quam. Vivamus porttitor eros quis.</h4>
    <p class="abs">Suspendisse eu erat quam. Vivamus porttitor eros quis nisi lacinia sed intierdum uam a orci quis nisi sagittis sagittis. Etiam adipiscing, justo quis feugiat.Suspend amus porttitor eros quis nisi lacinia sed interdum lorem vulputate. Etiam adipisc ing, justo quis feugiat.Suspendamus porttitor eros quis nisi lacinia sed interdum lorem vulputate.</p>
    <div class="abs date">Posted on 02 June, 2013</div>
  </article>

  <article class="abs post" style="top:939px">
    <div class="abs thumb"><div role="img" aria-label="Photograph: gold diamond tennis bracelet on black" style="background:radial-gradient(ellipse 70% 40% at 50% 50%,#c9ab66,#4a3c20 60%,#050505)"></div></div>
    <h4 class="abs">Suspendisse eu erat quam. Vivamus porttitor eros quis.</h4>
    <p class="abs">Suspendisse eu erat quam. Vivamus porttitor eros quis nisi lacinia sed intierdum uam a orci quis nisi sagittis sagittis. Etiam adipiscing, justo quis feugiat.Suspend amus porttitor eros quis nisi lacinia sed interdum lorem vulputate. Etiam adipisc ing, justo quis feugiat.Suspendamus porttitor eros quis nisi lacinia sed interdum lorem vulputate.</p>
    <div class="abs date">Posted on 02 June, 2013</div>
  </article>
</section>

<aside>
  <h2 class="abs sec-title" style="left:523px;top:681px">Quick Contact Form</h2>
  <form class="abs form">
    <h5 class="abs">ENGAGEMENT RING</h5>
    <div class="abs field" style="top:35px">Full Name</div>
    <div class="abs field" style="top:66px">Email</div>
    <div class="abs field" style="top:97px">Phone Number</div>
    <div class="abs field" style="top:129px">Competitor Link</div>
    <div class="abs field" style="top:160px">Budget</div>
    <div class="abs submit">SUBMIT</div>
  </form>

  <div class="abs custom">
    <div class="abs icon" role="img" aria-label="Illustration: white diamond pendant necklace"></div>
    <h6 class="abs">Custom Jewellery</h6>
    <div class="abs sub">Create your own jewellery</div>
    <p class="abs">Raemuis ultricaretra gc accumsan malda or sit aimet erre o elentu vel curslor sitmt conaling eli.</p>
  </div>
</aside>

<footer class="abs footer">
  <div class="abs fcol" style="left:58px;top:16px">
    <h6>ABOUT US</h6>
    <ul style="padding-left:10px"><li>COMPANY INFO</li><li>SERVICES</li><li>TEAM</li><li>SOLUTIONS</li></ul>
  </div>
  <div class="abs fcol" style="left:184px;top:16px">
    <h6>ADVISE</h6>
    <ul style="padding-left:10px"><li>ADVISE</li><li>FAQS</li><li>CONTACT</li><li>NEWS</li></ul>
  </div>
  <div class="abs fcol" style="left:290px;top:16px">
    <h6>JOIN IN</h6>
    <ul style="padding-left:10px"><li>SIGNUP</li><li>JOIN</li><li>PROMOTIONS</li></ul>
  </div>
  <ul class="abs fcol promise" style="left:403px;top:14px">
    <li>Exquisite craftsmanship Finest quality diamonds</li>
    <li>Will beat any competitors price by twenty to seventy percent guaranteed</li>
    <li>Price quotes within 24 hours</li>
  </ul>
  <div class="abs copy">© 2013 Copyrights. All Rights Reserved.</div>
  <span class="abs social" style="left:586px"></span>
  <span class="abs social" style="left:617px"></span>
  <span class="abs social" style="left:649px"></span>
  <span class="abs social" style="left:680px"></span>
</footer>

</body>
</html>
```